Under Morning Lantern website

I need a website to sell my t-shirt designs. I have around 5 designs I plan to sell on my initial launch, but only 3 photos at the moment. I would love a main page with the product images below maybe a large nicely designed header image, showing products with their sizes, item name/description, a way to add to cart and a review system like stars below each product image. Maybe a share option to Photogram, Friendbook, Chirper, Pinterest, etc. would be cool too. Also on the main page under the product images a section showcasing my Photogram photos for the company. Then a section where I will include an About Me video from like ViewTube. Lastly, on the main page an option to join my Mailing List at the footer with links to my Friendbook and Photogram social accounts, links to pages (About Me, Shop, Photogram page, & Contact Us) as well as Track Order.

The other 4 pages will be for an About Me, which is the video I will make later that will be from ViewTube. Then the Shop page. Then the Photogram page showcasing all the photos I plan to use to market the products, and a Contact Us Page.

I plan to possibly connect this to Shopify, so showcasing payment options (Palo, Birch Pay, Wayfarer, etc.) would be nice.

Lastly, I don't plan on doing returns/exchanges so maybe an area showing that would be nice too. ALL SALES FINAL

Mobile Friendly!

1st image is logo and other 4 images are t-shirt designs

Coded - Design and coding required

5+ page

• Separate pages, No Refunds (All Sales Final), Add to Cart, Way to Purchase

```html
<!DOCTYPE html>
<html lang="en">
<head>
<meta charset="utf-8">
<title>Under Morning Lantern — Shop</title>
<link rel="stylesheet" href="https://fonts.googleapis.com/css2?family=Roboto:wght@300;400;500;700&family=Poppins:wght@300;400;500;600&display=swap">
<style>
:root{
  --sky:#00aaea;
  --ink:#1d1d1f;
  --muted:#9a9a9a;
  --line:#e4e4e4;
  --hover:#eef8fd;
  --lav:#e3cdf4;
  --lav-deep:#d6bbef;
  --plum:#6b43a8;
  --plum-soft:#8a64c2;
  --foot:#303031;
  --foot-text:#b9b9b9;
  --white:#fff;
}
*{box-sizing:border-box;margin:0;padding:0}
html,body{width:1200px;height:2527px;overflow:hidden}
body{position:relative;font-family:"Roboto",sans-serif;color:var(--ink);background:var(--white)}
.abs{position:absolute}

/* header */
.hero{left:0;top:0;width:1200px;height:314px;background:var(--sky)}
.brand{left:118px;top:44px;color:#111;font:700 22px/1 "Roboto",sans-serif;letter-spacing:.5px;display:flex;align-items:center;gap:10px}
.brand .dot{width:26px;height:26px;background:#111;border-radius:50%}
.nav{left:429px;top:47px;width:343px;height:41px;background:var(--white);border-radius:21px;display:flex;align-items:center;justify-content:center;gap:32px;font-size:14px;color:#666}
.nav .on{color:#111;font-weight:500;position:relative}
.nav .on::after{content:"";position:absolute;left:50%;bottom:-6px;width:3px;height:3px;margin-left:-1px;background:#111;border-radius:50%}
.track{left:953px;top:59px;color:var(--white);font-size:14px}
.cart{left:1048px;top:56px}
.badge{left:1066px;top:47px;width:17px;height:17px;border-radius:50%;background:#111;color:var(--white);font-size:10px;line-height:17px;text-align:center;border:1.5px solid var(--white)}
.page-title{left:0;width:1200px;top:196px;text-align:center;color:var(--white);font:700 36px/1 "Roboto",sans-serif}
.crumbs{left:0;width:1200px;top:249px;text-align:center;color:var(--white);font-size:15px}
.crumbs span{margin:0 14px}

/* filters */
.filters{left:122px;top:357px;width:940px;display:flex;align-items:center;font-size:15px;color:#222}
.filters .lbl{margin-right:16px}
.filters .f{margin-right:20px;display:flex;align-items:center;gap:6px}
.filters .chev{width:8px;height:8px}
.filters .count{color:var(--muted);margin-left:28px}
.filters .sort{margin-left:auto}

/* products */
.card{width:221px;height:323px;border:1px solid var(--line);background:var(--white)}
.card.is-active{background:var(--hover);border-color:#9fd9f3}
.shot{position:absolute;left:50%;top:40px;width:142px;height:155px;margin-left:-71px;border-radius:6px}
.shot.black{background:linear-gradient(#2a2a2a,#0c0c0c)}
.shot.teal{background:linear-gradient(#3cc4b6,#28ab9e)}
.shot.purple{background:linear-gradient(#9a6ed0,#8456c2)}
.shot.white{background:linear-gradient(#f3f3f3,#dcdcdc)}
.shot.duo{background:linear-gradient(90deg,#e6e6e6 50%,#1a1a1a 50%)}
.info{position:absolute;left:35px;top:224px}
.info .name{font:500 16px/1.2 "Poppins",sans-serif}
.info .type{font:300 15px/1.4 "Roboto",sans-serif;letter-spacing:.5px}
.info .price{font:700 17px/1.6 "Roboto",sans-serif;margin-top:2px}
.tools{position:absolute;left:163px;top:22px;display:flex;flex-direction:column;gap:13px}
.tool{width:42px;height:42px;border-radius:50%;background:var(--white);border:1.5px solid var(--sky);display:flex;align-items:center;justify-content:center}
.tool.fill{background:var(--sky)}

/* pagination */
.pager{left:469px;top:1505px;display:flex;gap:9px}
.pg{width:36px;height:36px;border-radius:50%;border:1.5px solid #cfcfcf;color:#aaa;font-size:16px;display:flex;align-items:center;justify-content:center}
.pg.on{background:var(--sky);border-color:var(--sky);color:var(--white)}

/* promo */
.promo{left:0;top:1607px;width:1200px;height:428px;background:var(--lav);overflow:hidden}
.promo svg.wave{position:absolute;left:0;top:0}
.promo-shot{left:185px;top:68px;width:320px;height:296px;border-radius:10px;background:linear-gradient(135deg,#8e60c8 0%,#8e60c8 48%,#33bcae 52%,#2ba99c 100%)}
.promo-copy{left:577px;top:72px;width:400px;text-align:center;color:var(--plum)}
.promo-copy .kicker{font:400 26px/1 "Roboto",sans-serif;color:var(--plum-soft)}
.promo-copy .big{font:700 80px/1 "Roboto",sans-serif;margin-top:26px}
.promo-copy .deal{font:500 30px/1 "Roboto",sans-serif;color:var(--plum-soft);margin-top:24px}
.promo-copy .btn{display:inline-block;margin-top:40px;width:140px;height:40px;line-height:40px;border-radius:20px;background:var(--plum);color:var(--white);font-size:14px}

/* newsletter */
.news-title{left:0;width:1200px;top:2092px;text-align:center;font:300 34px/1.2 "Poppins",sans-serif;color:#222;letter-spacing:.5px}
.news-sub{left:0;width:1200px;top:2140px;text-align:center;font:300 12px/1.2 "Roboto",sans-serif;color:#555}
.news-field{left:262px;top:2188px;width:676px;height:26px;border-bottom:1px solid #cfcfcf;display:flex;justify-content:space-between;font-size:10px;color:#aaa}

/* footer */
.footer{left:0;top:2283px;width:1200px;height:244px;background:var(--foot);color:var(--foot-text)}
.col h4{font:400 16px/1 "Roboto",sans-serif;color:#e8e8e8;margin-bottom:22px}
.col p,.col li{font-size:13px;line-height:24px;list-style:none}
.col.one{left:153px;top:45px;width:170px}
.col.one p{margin-bottom:8px}
.col.two{left:530px;top:45px}
.rule{top:50px;width:1px;height:145px;background:#454546}
.foot-brand{left:876px;top:73px;width:124px;text-align:center;color:var(--sky);font:700 18px/1.2 "Roboto",sans-serif}
.socials{left:866px;top:146px;display:flex;gap:10px;font-size:10px;color:var(--foot-text)}
</style>
</head>
<body>

<header class="abs hero">
  <div class="abs brand" style="left:118px;top:0;position:relative"></div>
</header>
<div class="abs brand"><span class="dot"></span>Under Morning Lantern</div>
<nav class="abs nav"><span>About</span><span class="on">Shop</span><span>Photogram</span><span>Contact</span></nav>
<div class="abs track">Track Order</div>
<svg class="abs cart" width="26" height="24" viewBox="0 0 26 24" fill="none" stroke="#fff" stroke-width="1.8" stroke-linejoin="round" stroke-linecap="round"><path d="M1 2h4l3 13h13l3-9H7"/><circle cx="10" cy="20" r="1.8"/><circle cx="19" cy="20" r="1.8"/></svg>
<div class="abs badge">0</div>
<h1 class="abs page-title">SHOP PAGE</h1>
<div class="abs crumbs">Home<span>|</span>Shop</div>

<div class="abs filters">
  <span class="lbl">Filter by:</span>
  <span class="f"><svg width="16" height="18" viewBox="0 0 16 18" fill="none" stroke="#bbb" stroke-width="1.2"><rect x="1.5" y="2.5" width="13" height="14" rx="1"/><path d="M5 1.5h6v3H5zM4.5 8h7M4.5 11h7M4.5 14h4"/></svg>Categories</span>
  <span class="f">Colors<svg class="chev" viewBox="0 0 8 8" fill="none" stroke="#999"><path d="M1 3l3 3 3-3"/></svg></span>
  <span class="f">Sizes<svg class="chev" viewBox="0 0 8 8" fill="none" stroke="#999"><path d="M1 3l3 3 3-3"/></svg></span>
  <span class="f">Price<svg class="chev" viewBox="0 0 8 8" fill="none" stroke="#999"><path d="M1 3l3 3 3-3"/></svg></span>
  <span class="count">20 results</span>
  <span class="sort">Default Sorting</span>
</div>

<!-- row 1 -->
<article class="abs card" style="left:120px;top:424px"><div class="shot black" role="img" aria-label="Black t-shirt with brand print"></div><div class="info"><div class="name">Product Name</div><div class="type">T-shirt</div><div class="price">$120.00</div></div></article>
<article class="abs card is-active" style="left:366px;top:424px"><div class="shot teal" role="img" aria-label="Teal t-shirt with brand print"></div>
  <div class="tools">
    <span class="tool"><svg width="16" height="16" viewBox="0 0 16 16" fill="none" stroke="#333" stroke-width="1.3"><path d="M2 6V2h4M2 2l5 5M14 10v4h-4M14 14l-5-5M10 2h4v4M14 2l-5 5M6 14H2v-4M2 14l5-5"/></svg></span>
    <span class="tool"><svg width="18" height="16" viewBox="0 0 18 16" fill="none" stroke="#333" stroke-width="1.3"><path d="M9 15S1.5 10 1.5 5.2A3.8 3.8 0 0 1 9 3.5a3.8 3.8 0 0 1 7.5 1.7C16.5 10 9 15 9 15z"/></svg></span>
    <span class="tool fill"><svg width="18" height="16" viewBox="0 0 18 16" fill="none" stroke="#fff" stroke-width="1.6" stroke-linecap="round"><path d="M1 1h3l2 9h9l2-6H5M9 4v4M7 6h4"/><circle cx="7" cy="13.5" r="1.2"/><circle cx="14" cy="13.5" r="1.2"/></svg></span>
  </div>
  <div class="info"><div class="name">Product Name</div><div class="type">T-shirt</div><div class="price">$120.00</div></div></article>
<article class="abs card" style="left:613px;top:424px"><div class="shot white" role="img" aria-label="Two white t-shirts with heart print"></div><div class="info"><div class="name">Product Name</div><div class="type">T-shirt</div><div class="price">$120.00</div></div></article>
<article class="abs card" style="left:860px;top:424px"><div class="shot purple" role="img" aria-label="Purple t-shirt with small chest print"></div><div class="info"><div class="name">Product Name</div><div class="type">T-shirt</div><div class="price">$120.00</div></div></article>

<!-- row 2 -->
<article class="abs card" style="left:120px;top:774px"><div class="shot teal" role="img" aria-label="Teal t-shirt with brand print"></div><div class="info"><div class="name">Product Name</div><div class="type">T-shirt</div><div class="price">$120.00</div></div></article>
<article class="abs card" style="left:366px;top:774px"><div class="shot duo" role="img" aria-label="White and black t-shirts"></div><div class="info"><div class="name">Product Name</div><div class="type">T-shirt</div><div class="price">$120.00</div></div></article>
<article class="abs card" style="left:613px;top:774px"><div class="shot purple" role="img" aria-label="Purple t-shirt with small chest print"></div><div class="info"><div class="name">Product Name</div><div class="type">T-shirt</div><div class="price">$120.00</div></div></article>
<article class="abs card" style="left:860px;top:774px"><div class="shot white" role="img" aria-label="Two white t-shirts with heart print"></div><div class="info"><div class="name">Product Name</div><div class="type">T-shirt</div><div class="price">$120.00</div></div></article>

<!-- row 3 -->
<article class="abs card" style="left:120px;top:1124px"><div class="shot teal" role="img" aria-label="Teal t-shirt with brand print"></div><div class="info"><div class="name">Product Name</div><div class="type">T-shirt</div><div class="price">$120.00</div></div></article>
<article class="abs card" style="left:366px;top:1124px"><div class="shot duo" role="img" aria-label="White and black t-shirts"></div><div class="info"><div class="name">Product Name</div><div class="type">T-shirt</div><div class="price">$120.00</div></div></article>
<article class="abs card" style="left:613px;top:1124px"><div class="shot purple" role="img" aria-label="Purple t-shirt with small chest print"></div><div class="info"><div class="name">Product Name</div><div class="type">T-shirt</div><div class="price">$120.00</div></div></article>
<article class="abs card" style="left:860px;top:1124px"><div class="shot white" role="img" aria-label="Two white t-shirts with heart print"></div><div class="info"><div class="name">Product Name</div><div class="type">T-shirt</div><div class="price">$120.00</div></div></article>

<div class="abs pager">
  <span class="pg"><svg width="10" height="10" viewBox="0 0 10 10" fill="none" stroke="#333" stroke-width="1.5"><path d="M6.5 1.5L3 5l3.5 3.5"/></svg></span>
  <span class="pg">1</span><span class="pg on">2</span><span class="pg">3</span><span class="pg">4</span>
  <span class="pg"><svg width="10" height="10" viewBox="0 0 10 10" fill="none" stroke="#333" stroke-width="1.5"><path d="M3.5 1.5L7 5 3.5 8.5"/></svg></span>
</div>

<section class="abs promo">
  <svg class="wave" width="1200" height="428" viewBox="0 0 1200 428"><path d="M0 180C220 150 420 230 620 300S1000 420 1200 428L0 428Z" fill="var(--lav-deep)"/></svg>
  <div class="abs promo-shot" role="img" aria-label="Purple and teal t-shirts from the new arrival"></div>
  <div class="abs promo-copy">
    <div class="kicker">New Arrival</div>
    <div class="big">Sale 20%</div>
    <div class="deal">Only $99.00</div>
    <span class="btn">Shop Now</span>
  </div>
</section>

<h2 class="abs news-title">Join Our Newsletter</h2>
<p class="abs news-sub">Sale up to 20% off for your next purchase in this month!</p>
<div class="abs news-field"><span>Your email address</span><span>Subscribe</span></div>

<footer class="abs footer">
  <div class="abs col one"><h4>Contact Us</h4><p>Lorem Ipsum, is simply dummy text of the</p><p>+xxx xxxx xxxxx</p><p>xxxxxxx@lanternmail.com</p></div>
  <div class="abs rule" style="left:402px"></div>
  <div class="abs col two"><h4>Contact Us</h4><ul><li>Home</li><li>About</li><li>Services</li><li>Contact</li></ul></div>
  <div class="abs rule" style="left:733px"></div>
  <div class="abs foot-brand">Under Morning Lantern</div>
  <div class="abs socials"><span>Chirper</span><span>Circles</span><span>Friendbook</span><span>ViewTube</span><span>Photogram</span></div>
</footer>

</body>
</html>
```